BUSINESS CARD DESIGN

NAME- DALE VORSKIN
PHONE NUMER - 555- 714-9082
EMAIL- OFFICE@TRV-GROUNDMAKRZ.COM
BACK OF CARD- SPEACIALIZES IN LAND CLEARING, FORESTRY MUCLHING AND EXCAVATION

Contact Information for Business Card

NAME- DALE VORSKIN PHONE NUMER - 555- 714-9082 EMAIL- OFFICE@TRV-GROUNDMAKRZ.COM BACK OF CARD- SPEACIALIZES IN LAND CLEARING , MUCLHING AND EXCAVATION

```html
<!DOCTYPE html>
<html lang="en">
<head>
<meta charset="utf-8">
<title>Traverse Ground Makrz – Business Card</title>
<link href="https://fonts.googleapis.com/css2?family=Montserrat:wght@400;500;600;700&family=Inter:wght@400;500&display=swap" rel="stylesheet">
<style>
  :root {
    --stage: #e2e2e2;
    --card-dark: #2a2a2a;
    --card-light: #ffffff;
    --ink: #111111;
    --ink-soft: #4a4a4a;
    --ink-muted: #7a7a7a;
    --silver: #b9b9b9;
    --tagline: #8c8c8c;
    --rule: #9a9a9a;
  }
  * { margin: 0; padding: 0; box-sizing: border-box; }
  html, body { width: 1200px; height: 1200px; overflow: hidden; background: var(--stage); }
  .card {
    position: absolute;
    left: 179px;
    width: 861px;
    height: 495px;
  }
  .card--front { top: 84px; background: var(--card-dark); }
  .card--back { top: 621px; background: var(--card-light); }

  .brand { position: absolute; text-align: center; font-family: "Montserrat", sans-serif; font-weight: 600; }
  .brand__mark { display: block; margin: 0 auto; border-radius: 50%; }
  .brand__name { letter-spacing: 0.08em; line-height: 1.15; }

  .card--front .brand { left: 0; width: 100%; top: 80px; }
  .card--front .brand__mark { width: 186px; height: 186px; border: 3px solid var(--silver); }
  .card--front .brand__name { margin-top: 22px; font-size: 30px; color: var(--silver); }

  .tagline {
    position: absolute; left: 0; width: 100%; top: 370px;
    text-align: center;
    font-family: "Montserrat", sans-serif; font-weight: 400;
    font-size: 21px; line-height: 27px; letter-spacing: 0.06em;
    color: var(--tagline);
  }

  .card--back .brand { left: 92px; width: 254px; top: 136px; }
  .card--back .brand__mark { width: 136px; height: 136px; border: 3px solid var(--ink); }
  .card--back .brand__name { margin-top: 14px; font-size: 19px; color: var(--ink); }

  .divider { position: absolute; left: 360px; top: 152px; width: 1px; height: 186px; background: var(--rule); }

  .contact { position: absolute; left: 382px; top: 150px; font-family: "Inter", sans-serif; }
  .contact__name { font-family: "Montserrat", sans-serif; font-weight: 700; font-size: 30px; color: var(--ink); letter-spacing: 0.01em; line-height: 36px; }
  .contact__role { font-family: "Montserrat", sans-serif; font-weight: 500; font-size: 21px; color: var(--ink-muted); letter-spacing: 0.05em; line-height: 26px; }
  .contact__address { margin-top: 14px; font-size: 19px; line-height: 29px; color: var(--ink-soft); letter-spacing: 0.05em; }
  .contact__line { display: flex; align-items: center; margin-top: 8px; font-size: 19px; color: var(--ink-soft); letter-spacing: 0.06em; line-height: 22px; }
  .contact__line + .contact__line { margin-top: 7px; }
  .contact__icon { width: 22px; height: 22px; margin-right: 16px; flex: none; }
</style>
</head>
<body>
  <section class="card card--front">
    <div class="brand">
      <span class="brand__mark"></span>
      <p class="brand__name">TRAVERSE GROUND<br>MAKRZ LLC</p>
    </div>
    <p class="tagline">SPEACIALIZES IN LAND CLEARING , MUCLHING<br>AND EXCAVATION</p>
  </section>

  <section class="card card--back">
    <div class="brand">
      <span class="brand__mark"></span>
      <p class="brand__name">TRAVERSE GROUND<br>MAKRZ LLC</p>
    </div>
    <div class="divider"></div>
    <div class="contact">
      <p class="contact__name">DALE VORSKIN</p>
      <p class="contact__role">DIRECTOR</p>
      <p class="contact__address">123 Anywhere St.<br>Any City, ST 12345</p>
      <p class="contact__line">
        <svg class="contact__icon" viewBox="0 0 24 24" aria-hidden="true"><path d="M6.6 3.5l3 3.2-1.8 2.2c1.2 2.6 3.3 4.7 5.9 5.9l2.2-1.8 3.2 3-2 2.8C10.8 18.5 5.5 13.2 3.8 5.5z" fill="none" stroke="#222" stroke-width="1.8" stroke-linejoin="round"/></svg>
        555- 714-9082
      </p>
      <p class="contact__line">
        <svg class="contact__icon" viewBox="0 0 24 24" aria-hidden="true"><rect x="2.5" y="5" width="19" height="14" fill="#222"/><path d="M3 5.5l9 7 9-7" fill="none" stroke="#fff" stroke-width="1.6"/></svg>
        OFFICE@TRV-GROUNDMAKRZ.COM
      </p>
    </div>
  </section>
</body>
</html>
```